Business Card Design Project

After recently finishing a design project for the company logo using markbazaar, it's now time for a business card. Attached to this is the logo.

The requirements for the business card are pretty straightforward:

- A clean, uncomplicated look
- Consistent usage of fonts
- Designs for both single sided and double sided cards
- A modern layout with preferably space to refer to social media accounts and/or downloadable vcards through a qr code
- consistent application of the company colour scheme: red/white. Hex codes for exact colour can be provided

Thanks!

```html
<!DOCTYPE html>
<html lang="en">
<head>
<meta charset="utf-8">
<title>Keystone Talent – Business Card</title>
<link href="https://fonts.googleapis.com/css2?family=Source+Sans+3:wght@400;600;700&display=swap" rel="stylesheet">
<style>
  :root {
    --bg: #e9e6e2;
    --card: #ffffff;
    --ink: #231f20;
    --ink-soft: #333333;
    --brand-red: #e31e26;
  }
  * { box-sizing: border-box; margin: 0; padding: 0; }
  html, body {
    width: 960px;
    height: 1200px;
    overflow: hidden;
    background: var(--bg);
    font-family: "Source Sans 3", "Myriad Pro", Arial, sans-serif;
    color: var(--ink);
  }
  .canvas { position: relative; width: 960px; height: 1200px; }

  .card {
    position: absolute;
    width: 840px;
    height: 479px;
    background: var(--card);
    border-radius: 32px;
    box-shadow: 0 4px 10px rgba(0,0,0,0.18);
  }
  .card--front { left: 55px; top: 93px; }
  .card--back  { left: 60px; top: 638px; }

  .brand {
    position: absolute;
    left: 0; right: 0;
    display: flex;
    align-items: center;
    justify-content: center;
    gap: 22px;
  }
  .card--front .brand { top: 102px; }
  .card--back .brand  { top: 160px; }
  .brand__square {
    width: 64px;
    height: 64px;
    background: var(--brand-red);
    flex: none;
  }
  .brand__name {
    font-size: 72px;
    font-weight: 600;
    letter-spacing: -1px;
    color: var(--ink);
    line-height: 1;
  }

  .holder {
    position: absolute;
    top: 296px;
    left: 0; right: 0;
    text-align: center;
    font-size: 25px;
    color: var(--ink-soft);
  }
  .holder__name { font-weight: 700; }
  .holder__role { font-size: 21px; font-weight: 400; }

  .contact {
    position: absolute;
    left: 68px;
    top: 356px;
    list-style: none;
    font-size: 20px;
    line-height: 35px;
    color: var(--ink-soft);
  }
  .contact__label { font-weight: 700; font-style: italic; }

  .address {
    position: absolute;
    left: 476px;
    top: 398px;
    font-style: normal;
    font-size: 20px;
    line-height: 29px;
    color: var(--ink-soft);
  }
</style>
</head>
<body>
<main class="canvas">
  <section class="card card--front">
    <div class="brand">
      <span class="brand__square"></span>
      <span class="brand__name">Keystone Talent</span>
    </div>
    <p class="holder"><span class="holder__name">Your Name -</span> <span class="holder__role">Designation</span></p>
    <ul class="contact">
      <li><span class="contact__label">t</span> : 123-123-1234</li>
      <li><span class="contact__label">e</span> : info@yourwebsite.com</li>
      <li><span class="contact__label">w</span> : www.keystonetalent.com</li>
    </ul>
    <address class="address">1234, Street Name<br>District, City, Country Code.</address>
  </section>

  <section class="card card--back">
    <div class="brand">
      <span class="brand__square"></span>
      <span class="brand__name">Keystone Talent</span>
    </div>
  </section>
</main>
</body>
</html>
```